Brell Stone Company Business Cards

Front and Back Business Card - logo and text setup - cool design. I need workable photoshop or illustrator files so I can setup each employee card with design that is created
Updates

Hi everyone, thank you for the great entries. Please no more white and blue cards - there are so many already - black and silver only now please. thanks!

Target Market(s)

Construction Industry - Facility Managers

Industry/Entity Type

Construction

Contact Information for Business Card

I really like contemporary simplistic looks - clean neat....not opposed to seeing some black backrounds

Requirements
Must have
• Logo/website address with design on front only - www.brellstone-example.com (logo attached)
• Back:
• Name/Title/Company Address/Phone/email address
Nice to have
• Cool design
Should not have
• Nothing gimmicky like Fire or Water - since we are a Fire Protection company - it has all been done

```html
<!DOCTYPE html>
<html lang="en">
<head>
<meta charset="utf-8">
<title>Brell Stone Company Business Cards</title>
<link rel="stylesheet" href="https://fonts.googleapis.com/css2?family=Open+Sans:ital,wght@0,400;0,600;0,800;1,700&display=swap">
<style>
  :root {
    --stage: #2a2a2c;
    --card-black: #030303;
    --brand-blue: #0a24a0;
    --brand-red: #f4241c;
    --text-white: #ffffff;
    --text-soft: #e9ecf6;
  }
  * { box-sizing: border-box; margin: 0; padding: 0; }
  html, body {
    width: 1200px; height: 960px; overflow: hidden;
    background: var(--stage);
    font-family: "Open Sans", Arial, sans-serif;
  }
  .sheet {
    width: 1200px; height: 960px;
    display: flex; flex-direction: column; align-items: center; justify-content: center;
    gap: 40px;
  }
  .card {
    position: relative;
    width: 760px; height: 434px;
    background: var(--card-black);
    overflow: hidden;
    box-shadow: 0 10px 30px rgba(0,0,0,.45);
  }
  .wordmark {
    font-weight: 800;
    color: var(--brand-red);
    letter-spacing: -1px;
    line-height: 1;
  }
  /* Front */
  .card-front .wordmark {
    position: absolute; left: 0; right: 0; top: 140px;
    text-align: center; font-size: 84px;
  }
  .card-front .web {
    position: absolute; left: 0; right: 0; top: 268px;
    text-align: center; color: var(--text-white);
    font-size: 19px; letter-spacing: 4px;
  }
  /* Back */
  .card-back .swoosh { position: absolute; inset: 0; width: 760px; height: 434px; }
  .card-back .wordmark {
    position: absolute; left: 44px; top: 92px; font-size: 58px;
  }
  .contact {
    position: absolute; right: 46px; top: 148px;
    text-align: right; color: var(--text-soft);
    font-size: 18px; line-height: 1.38;
  }
  .contact .name, .contact .title {
    font-weight: 700; font-style: italic; color: var(--text-white); font-size: 19px;
  }
  .contact .address { margin-top: 8px; }
  .contact .lines { margin-top: 14px; }
  .contact .line { display: flex; justify-content: flex-end; align-items: center; gap: 12px; }
  .contact .line svg { width: 16px; height: 16px; flex: none; }
</style>
</head>
<body>
<main class="sheet">
  <section class="card card-front" aria-label="Business card front">
    <div class="wordmark">Brell Stone</div>
    <div class="web">www.brellstone-example.com</div>
  </section>

  <section class="card card-back" aria-label="Business card back">
    <svg class="swoosh" viewBox="0 0 760 434" aria-hidden="true">
      <path d="M398 0 C418 160 318 380 112 434 L760 434 L760 0 Z" fill="var(--brand-red)"/>
      <path d="M411 0 C431 160 331 380 128 434 L760 434 L760 0 Z" fill="var(--card-black)"/>
      <path d="M418 0 C438 160 338 380 138 434 L760 434 L760 0 Z" fill="var(--brand-blue)"/>
    </svg>
    <div class="wordmark">Brell Stone</div>
    <div class="contact">
      <div class="name">Dana Whitfield</div>
      <div class="title">President</div>
      <div class="address">48 Harbor Point Road<br>Millbrook, NY 10990</div>
      <div class="lines">
        <div class="line">(555) 014-2290
          <svg viewBox="0 0 16 16" aria-hidden="true"><path d="M4 1 L6.5 4.5 L5 6.5 C6 8.5 7.5 10 9.5 11 L11.5 9.5 L15 12 L13 15 C7 14.5 1.5 9 1 3 Z" fill="#fff"/></svg>
        </div>
        <div class="line">info@brellstone-example.com
          <svg viewBox="0 0 16 16" aria-hidden="true"><rect x="1" y="3" width="14" height="10" fill="#fff"/><path d="M1 3 L8 9 L15 3" fill="none" stroke="var(--brand-blue)" stroke-width="1.4"/></svg>
        </div>
        <div class="line">www.brellstone-example.com
          <svg viewBox="0 0 16 16" aria-hidden="true"><g fill="none" stroke="#fff" stroke-width="1.3"><circle cx="8" cy="8" r="6.5"/><ellipse cx="8" cy="8" rx="3" ry="6.5"/><path d="M1.5 8 H14.5 M3 4.5 H13 M3 11.5 H13"/></g></svg>
        </div>
      </div>
    </div>
  </section>
</main>
</body>
</html>
```